Gestaltung Akt Kalender (Foto´s vorhanden und bearbeitet)
Zielgruppe
Einzel- & Großhandel mit Eisenwaren und Werkzeugen. Zielgruppe: Handwerk und Industrie.
Aufgabenstellung
Aus professionellen schwarz/weiß Aufnahmen soll ein Akt Kalender in der Größe 42x42 cm erstellt werden. Der Kalender soll an unsere Kunden aus dem Bereich Handwerk und Industrie verteilt werden. In den Bildern sind jeweils Artikel aus unserem Sortiment eingearbeitet. Ebenfalls soll das Logo des Herstellern und unser Logo - evtl. noch ein Spruch - auf jede Kalenderseite. Zusätzlich soll es ein Titelbild geben. Die Bilder sind bereits bearbeitet!

```html
<!DOCTYPE html>
<html lang="de">
<head>
<meta charset="utf-8">
<title>Kalender 2014 – Titel und Rückseite</title>
<link href="https://fonts.googleapis.com/css2?family=Great+Vibes&family=Open+Sans:wght@300;400;600;700&display=swap" rel="stylesheet">
<style>
  :root {
    --stage: #c9c9c9;
    --cover-black: #0a0a0a;
    --photo-mid: #3a3a3a;
    --band-grey: rgba(150,150,150,0.45);
    --white: #ffffff;
    --brand-violet: #3a1a8a;
    --text-dark: #1a1a1a;
  }
  * { margin: 0; padding: 0; box-sizing: border-box; }
  html, body { width: 1200px; height: 900px; overflow: hidden; }
  body {
    background: var(--stage);
    font-family: "Open Sans", Arial, sans-serif;
    position: relative;
  }
  .card {
    position: absolute;
    top: 180px;
    width: 540px;
    height: 540px;
    overflow: hidden;
  }
  /* Titelseite */
  .cover { left: 40px; background: var(--cover-black); }
  .cover-photo {
    position: absolute; inset: 0;
    background: radial-gradient(ellipse 45% 70% at 62% 45%, var(--photo-mid) 0%, #1c1c1c 55%, var(--cover-black) 100%);
  }
  .cover-brand {
    position: absolute; left: 48px; top: 80px;
    color: var(--white);
    font-size: 30px; font-weight: 400; letter-spacing: 1px;
  }
  .cover-script {
    position: absolute; left: 70px; top: 318px;
    font-family: "Great Vibes", cursive;
    font-size: 74px;
    color: rgba(255,255,255,0.16);
    white-space: nowrap;
  }
  .cover-band {
    position: absolute; left: 0; right: 0; top: 385px; height: 70px;
    background: var(--band-grey);
  }
  .cover-title {
    position: absolute; right: 45px; top: 396px;
    color: var(--white);
    font-size: 40px; font-weight: 300;
    white-space: nowrap;
  }
  .cover-icons {
    position: absolute; right: 45px; top: 470px;
    width: 90px; height: 20px;
    background: #d8d8d8;
  }
  /* Rückseite */
  .back { left: 620px; background: var(--white); }
  .back-header {
    position: absolute; right: 36px; top: 52px;
    width: 236px;
  }
  .back-brand {
    color: var(--brand-violet);
    font-size: 36px; font-weight: 400; line-height: 44px;
    white-space: nowrap;
  }
  .back-address {
    margin-top: 30px;
    color: var(--text-dark);
    font-size: 9px; line-height: 13px; font-style: normal;
    white-space: nowrap;
  }
  .back-icons {
    position: absolute; left: 45px; top: 405px;
    width: 200px; height: 42px;
    background: var(--brand-violet);
  }
  .back-band {
    position: absolute; left: 0; right: 0; top: 472px; height: 32px;
    background: var(--brand-violet);
  }
  .back-url {
    position: absolute; right: 40px; top: 4px;
    color: var(--white);
    font-size: 16px; font-weight: 700;
    white-space: nowrap;
  }
</style>
</head>
<body>
  <section class="card cover">
    <div class="cover-photo" role="img" aria-label="Schwarz-weiß Aktfoto einer Frau mit großem Maulschlüssel vor dunklem Hintergrund"></div>
    <div class="cover-brand">BRANDTNER</div>
    <div class="cover-script">Kalender 2014</div>
    <div class="cover-band"></div>
    <div class="cover-title">Kalender 2014</div>
    <div class="cover-icons" role="img" aria-label="Piktogramme: Bohrmaschine, Schrauben, Spaten, Hammer"></div>
  </section>

  <section class="card back">
    <div class="back-header">
      <div class="back-brand">BRANDTNER</div>
      <address class="back-address">
        Konrad Brandtner e.K. · Lindenplatz 4 · 01234 Talheim<br>
        Tel. 01234/5670100 · Fax 01234/5670122<br>
        E-Mail: info@brandtner-werkzeug.de
      </address>
    </div>
    <div class="back-icons" role="img" aria-label="Piktogramme: Bohrmaschine, Schrauben, Spaten, Hammer"></div>
    <div class="back-band">
      <div class="back-url">www.brandtner-werkzeug.de</div>
    </div>
  </section>
</body>
</html>
```